International Business Development Firm, in need of Branded Stationery material

We just made our Logo and now we are looking for branded stationery for our company such as:

* A Letterhead with our company's name, address, and logo at the top in Word format for easy editing
* A more formal letter format with a light background design (watermark) featuring our logo, allowing us to write over it for various documents and presentations
* Business card + Envelopes are a plus but not a must
* PowerPoint for company and product introductions
* An Info sheet with Bullet Points

The design should be professional.
Please ensure the design is high quality and print ready.

Target Market(s)

Businesses and high net value individuels

Industry/Entity Type

International Business Development Firm

Colors

Designer to choose colors to be used in the design.

Requirements
Must have
• word docs so i can use the stationery templates afterwards

```html
<!DOCTYPE html>
<html lang="en">
<head>
<meta charset="utf-8">
<title>Violeta Ventures – Card</title>
<link href="https://fonts.googleapis.com/css2?family=Montserrat:wght@600&family=Open+Sans:wght@400;700&display=swap" rel="stylesheet">
<style>
  :root {
    --paper: #e6e6e8;
    --violet: #6c3f98;
    --violet-band: #8a62b0;
    --band-text: #ecebf0;
    --trim: #d27ac4;
  }
  html, body {
    margin: 0;
    padding: 0;
    overflow: hidden;
    background: var(--paper);
  }
  .card {
    position: relative;
    width: 1200px;
    height: 900px;
    background: var(--paper);
    overflow: hidden;
  }
  .trim-line {
    position: absolute;
    inset: 10px;
    border: 1px solid var(--trim);
    pointer-events: none;
  }
  .brand {
    position: absolute;
    display: flex;
    align-items: center;
    gap: 28px;
    font-family: "Montserrat", sans-serif;
    font-weight: 600;
    color: var(--violet);
  }
  .brand-dot {
    flex: none;
    border-radius: 50%;
    background: var(--violet);
  }
  .brand-name {
    display: flex;
    flex-direction: column;
    align-items: center;
    line-height: 1;
  }
  .brand--primary {
    left: 235px;
    top: 120px;
  }
  .brand--primary .brand-dot { width: 96px; height: 96px; }
  .brand--primary .brand-line1 { font-size: 84px; letter-spacing: 1px; }
  .brand--primary .brand-line2 { font-size: 36px; letter-spacing: 14px; margin-top: 14px; }
  .brand--secondary {
    left: 0;
    right: 0;
    top: 525px;
    justify-content: center;
  }
  .brand--secondary .brand-line1 { font-size: 56px; letter-spacing: 1px; }
  .brand--secondary .brand-line2 { font-size: 26px; letter-spacing: 10px; margin-top: 12px; }
  .tagline-band {
    position: absolute;
    left: 0;
    top: 410px;
    width: 1200px;
    height: 80px;
    background: var(--violet-band);
    display: flex;
    align-items: center;
    justify-content: center;
  }
  .tagline {
    margin: 0;
    font-family: "Open Sans", sans-serif;
    font-weight: 700;
    font-size: 45px;
    color: var(--band-text);
    letter-spacing: 0.2px;
  }
  .contact {
    position: absolute;
    left: 52px;
    top: 688px;
    margin: 0;
    font-family: "Open Sans", sans-serif;
    font-weight: 400;
    font-size: 40px;
    line-height: 54px;
    color: var(--violet);
    letter-spacing: -0.5px;
  }
  .contact span { display: block; white-space: nowrap; }
</style>
</head>
<body>
  <main class="card">
    <div class="trim-line"></div>

    <div class="brand brand--primary">
      <span class="brand-dot"></span>
      <span class="brand-name">
        <span class="brand-line1">VIOLETA</span>
        <span class="brand-line2">VENTURES</span>
      </span>
    </div>

    <div class="tagline-band">
      <h1 class="tagline">International Business Development Firm</h1>
    </div>

    <div class="brand brand--secondary">
      <span class="brand-name">
        <span class="brand-line1">VIOLETA</span>
        <span class="brand-line2">VENTURES</span>
      </span>
    </div>

    <address class="contact">
      <span>Address: aaaaaaaa, bbbbbbbb, cccccccccc-</span>
      <span>Phone: 0000000000, E mail: violetaventures.com,</span>
      <span>Web: www.violeta.com</span>
    </address>
  </main>
</body>
</html>
```